Business Card Design for Training Business

Clear Path Coaching is a new business that delivers training and other services with a focus on topics related to mental health and wellbeing, for example, Wellmind Response Course, Resilience etc. We have a strong focus on evidence-based psychology and neuroscience. I have a logo which I will upload with the brief, so please consider colours that work well with the logo.
Target Market(s)
Adults, workplaces (particularly government and not-for-profits)
Industry/Entity Type
Business
Contact Information for Business Card
Head Strong TrainingSamantha SellwoodDirector0438 770 850sam@headstrongtraining.com.auwww.headstrongtraining.com.au

```html
<!DOCTYPE html>
<html lang="en">
<head>
<meta charset="utf-8">
<title>Clear Path Coaching – Business Card</title>
<link rel="stylesheet" href="https://fonts.googleapis.com/css2?family=Open+Sans:wght@300;400;600&display=swap">
<style>
  :root {
    --canvas-bg: #e9e7e3;
    --card-black: #0b0b0c;
    --card-sheen: #1c1c1e;
    --teal: #3cc2c6;
    --teal-deep: #2aa3a8;
    --text-light: #e8e8e8;
    --text-soft: #b9b9b9;
  }
  * { margin: 0; padding: 0; box-sizing: border-box; }
  html, body {
    width: 1200px; height: 1023px; overflow: hidden;
    background: var(--canvas-bg);
    font-family: "Open Sans", Arial, sans-serif;
  }
  .canvas {
    width: 1200px; height: 1023px;
    display: flex; flex-direction: column; align-items: center; justify-content: center;
    gap: 60px;
  }
  .card {
    position: relative;
    width: 720px; height: 411px;
    border-radius: 10px;
    background: linear-gradient(150deg, var(--card-sheen) 0%, var(--card-black) 55%);
    box-shadow: 0 14px 30px rgba(0,0,0,0.25);
    overflow: hidden;
    color: var(--text-light);
  }
  .edge-tab {
    position: absolute;
    width: 26px; height: 120px;
    background: var(--teal);
    border-radius: 0 14px 14px 0;
  }
  .card-front .edge-tab { left: 0; top: 236px; }
  .card-back .edge-tab { right: 0; top: 60px; border-radius: 14px 0 0 14px; }

  /* Front */
  .brand {
    position: absolute; right: 70px; top: 62px;
    display: flex; align-items: center; gap: 22px;
  }
  .brand-dot {
    width: 64px; height: 64px; border-radius: 50%;
    border: 2px solid var(--teal);
  }
  .brand-name {
    font-weight: 300; font-size: 30px; letter-spacing: 3px;
    text-transform: uppercase; color: var(--text-light); line-height: 1.15;
  }
  .divider {
    position: absolute; left: 70px; right: 70px; top: 196px;
    height: 1px; background: var(--teal); opacity: 0.7;
  }
  .person {
    position: absolute; left: 70px; top: 226px;
  }
  .person-name { font-size: 25px; font-weight: 400; color: var(--text-light); }
  .person-role { font-size: 17px; font-weight: 600; color: var(--teal); margin-top: 2px; }
  .person-company { font-size: 17px; font-weight: 600; color: var(--text-light); margin-top: 2px; }
  .contact-list {
    position: absolute; left: 330px; top: 236px;
    list-style: none;
  }
  .contact-item {
    display: flex; align-items: center; gap: 12px;
    font-size: 15px; font-weight: 400; color: var(--text-soft);
    margin-bottom: 14px;
  }
  .contact-icon { width: 18px; height: 18px; flex: none; }

  /* Back */
  .card-back .brand {
    right: auto; top: 50%; left: 50%;
    transform: translate(-50%, -50%);
    flex-direction: column; gap: 20px; text-align: center;
  }
  .card-back .brand-dot { width: 96px; height: 96px; }
</style>
</head>
<body>
<main class="canvas">
  <section class="card card-front" aria-label="Business card front">
    <div class="brand">
      <span class="brand-dot"></span>
      <div class="brand-name">Clear Path<br>Coaching</div>
    </div>
    <div class="divider"></div>
    <span class="edge-tab"></span>
    <div class="person">
      <div class="person-name">Rebecca Tanfield</div>
      <div class="person-role">Manager</div>
      <div class="person-company">Clear Path Coaching</div>
    </div>
    <ul class="contact-list">
      <li class="contact-item">
        <svg class="contact-icon" viewBox="0 0 24 24"><path fill="var(--teal)" d="M6.6 10.8a15.1 15.1 0 0 0 6.6 6.6l2.2-2.2a1 1 0 0 1 1-.25 11.4 11.4 0 0 0 3.6.57 1 1 0 0 1 1 1V20a1 1 0 0 1-1 1A17 17 0 0 1 3 4a1 1 0 0 1 1-1h3.5a1 1 0 0 1 1 1c0 1.25.2 2.45.57 3.57a1 1 0 0 1-.25 1z"/></svg>
        0491 362 517
      </li>
      <li class="contact-item">
        <svg class="contact-icon" viewBox="0 0 24 24"><rect x="2" y="5" width="20" height="14" rx="2" fill="var(--teal)"/><path d="M3 6l9 7 9-7" fill="none" stroke="var(--card-black)" stroke-width="1.6"/></svg>
        bec@clearpathcoaching.example.au
      </li>
      <li class="contact-item">
        <svg class="contact-icon" viewBox="0 0 24 24"><circle cx="12" cy="12" r="10" fill="var(--teal)"/><g fill="none" stroke="var(--card-black)" stroke-width="1.3"><ellipse cx="12" cy="12" rx="4.5" ry="10"/><path d="M2 12h20M4 7h16M4 17h16"/></g></svg>
        www.clearpathcoaching.example.au
      </li>
    </ul>
  </section>

  <section class="card card-back" aria-label="Business card back">
    <span class="edge-tab"></span>
    <div class="brand">
      <span class="brand-dot"></span>
      <div class="brand-name">Clear Path<br>Coaching</div>
    </div>
  </section>
</main>
</body>
</html>
```